Stationery & Envelope Design

Executive Style looking stationery & envelope design.
Business Information:
TKL Executive Realty
2875 Birchwood Lane, Roseville, CA 95661-4180
Phone: 916.555.0142
Fax: 916.555.0187

Industry/Entity Type

Business

```html
<!DOCTYPE html>
<html lang="en">
<head>
<meta charset="utf-8">
<title>TKL Executive Realty – Stationery</title>
<link rel="stylesheet" href="https://fonts.googleapis.com/css2?family=Open+Sans:wght@400;600&display=swap">
<style>
  :root{
    --stage:#efece8;
    --paper:#ffffff;
    --paper-shade:#ececec;
    --green:#5f9a0a;
    --blue:#1a34a6;
    --blue-deep:#0a1c86;
    --blue-bright:#2346d2;
    --orange:#f07d0c;
    --ink:#222222;
    --rule:#555555;
    --label:#3a3a3a;
  }
  *{box-sizing:border-box;margin:0;padding:0}
  html,body{width:1200px;height:525px;overflow:hidden}
  body{background:var(--stage);font-family:"Open Sans",Arial,sans-serif;color:var(--ink);position:relative}

  .sheet{position:absolute;top:22px;width:350px;height:452px;background:var(--paper);box-shadow:0 2px 6px rgba(0,0,0,.25);overflow:hidden}
  .sheet--letter{left:10px}
  .sheet--fax{left:397px;background:linear-gradient(135deg,#fff 0%,#f5f5f5 55%,var(--paper-shade) 100%)}

  .brand{position:absolute;display:flex;align-items:center;gap:5px;font-weight:400;font-size:9px;color:var(--blue);white-space:nowrap}
  .brand__mark{width:8px;height:8px;border-radius:50%;background:var(--green)}
  .sheet .brand{left:9px;top:32px}

  .contact{position:absolute;left:252px;top:7px;border-left:1px solid var(--rule);padding-left:5px;font-size:7.2px;line-height:9px;color:var(--ink);font-style:normal}

  .footer-band{position:absolute;left:0;right:0;bottom:0;height:34px;background:var(--green)}
  .footer-rule{position:absolute;left:0;right:0;height:3px}
  .footer-rule--orange{bottom:42px;background:var(--orange)}
  .footer-rule--blue{bottom:37px;background:var(--blue)}
  .tagline{position:absolute;color:#fff;font-size:9px;letter-spacing:.4px;white-space:nowrap;bottom:12px;right:16px}

  .fax__title{position:absolute;left:14px;top:96px;font-size:21px;font-weight:400;letter-spacing:.5px}
  .fax__fields{position:absolute;left:14px;top:134px;width:297px}
  .fax__row{display:flex;height:19px;align-items:flex-end;border-bottom:1px solid var(--rule);font-size:5.3px;color:var(--label);padding-bottom:1px}
  .fax__row span:first-child{width:176px}
  .fax__checks{position:absolute;left:13px;top:224px;display:flex;font-size:5.3px;color:var(--label)}
  .fax__check{display:flex;align-items:center;gap:4px}
  .fax__check i{display:block;width:7px;height:7px;border:1px solid #333;background:#fff}
  .fax__check:nth-child(1){width:46px}
  .fax__check:nth-child(2){width:59px}
  .fax__check:nth-child(3){width:75px}
  .fax__check:nth-child(4){width:65px}

  .envelope{position:absolute;overflow:hidden;box-shadow:0 2px 6px rgba(0,0,0,.3)}
  .envelope--back-green{left:802px;top:24px;width:389px;height:174px;background:var(--paper)}
  .envelope--back-blue{left:790px;top:99px;width:391px;height:150px;background:linear-gradient(180deg,#f3f3f3,#dedede)}
  .envelope--front{left:764px;top:188px;width:390px;height:175px;background:linear-gradient(135deg,#f4f4f4,#fff 60%)}
  .flap{position:absolute;left:0;top:0;width:100%;display:block}
  .flap-name{position:absolute;left:0;right:0;text-align:center;font-weight:400;font-size:10px;color:#fff}
  .envelope--back-green .flap-name{top:30px}
  .envelope--back-blue .flap-name{top:31px}

  .envelope--front .brand{left:10px;top:12px}
  .envelope__address{position:absolute;left:10px;top:42px;font-size:7.2px;line-height:9px;font-style:normal}

  .option-label{position:absolute;top:490px;font-size:21px;color:#333;width:200px;text-align:center}
  .option-label--1{left:85px}
  .option-label--2{left:472px}
</style>
</head>
<body>

  <section class="sheet sheet--letter">
    <div class="brand"><span class="brand__mark"></span>TKL Executive Realty</div>
    <address class="contact">2875 Birchwood Lane<br>Roseville, CA 95661-4180<br>✆ 916.555.0142<br>✆ 916.555.0187</address>
    <div class="footer-rule footer-rule--orange"></div>
    <div class="footer-rule footer-rule--blue"></div>
    <div class="footer-band"></div>
    <span class="tagline">Homes found with care</span>
  </section>

  <section class="sheet sheet--fax">
    <div class="brand"><span class="brand__mark"></span>TKL Executive Realty</div>
    <address class="contact">2875 Birchwood Lane<br>Roseville, CA 95661-4180<br>✆ 916.555.0142<br>✆ 916.555.0187</address>
    <h1 class="fax__title">FAX</h1>
    <div class="fax__fields">
      <div class="fax__row"><span>To :</span><span>From :</span></div>
      <div class="fax__row"><span>Fax :</span><span>Pages :</span></div>
      <div class="fax__row"><span>Phone :</span><span>Date :</span></div>
      <div class="fax__row"><span>Re :</span><span>CC :</span></div>
    </div>
    <div class="fax__checks">
      <span class="fax__check"><i></i>Urgent</span>
      <span class="fax__check"><i></i>For Review</span>
      <span class="fax__check"><i></i>Please Comment</span>
      <span class="fax__check"><i></i>Please Reply</span>
      <span class="fax__check"><i></i>Please Recycle</span>
    </div>
    <div class="footer-rule footer-rule--orange"></div>
    <div class="footer-rule footer-rule--blue"></div>
    <div class="footer-band"></div>
    <span class="tagline">Homes found with care</span>
  </section>

  <section class="envelope envelope--back-green">
    <svg class="flap" viewBox="0 0 389 72" width="389" height="72" aria-hidden="true">
      <path d="M0,0 H389 V20 L194,70 L0,20 Z" fill="var(--green)"/>
    </svg>
    <div class="flap-name">TKL Executive Realty</div>
  </section>

  <section class="envelope envelope--back-blue">
    <svg class="flap" viewBox="0 0 391 72" width="391" height="72" aria-hidden="true">
      <defs>
        <radialGradient id="flapBlue" cx="50%" cy="30%" r="70%">
          <stop offset="0" stop-color="var(--blue-bright)"/>
          <stop offset="1" stop-color="var(--blue-deep)"/>
        </radialGradient>
      </defs>
      <path d="M0,0 H391 V22 L195,70 L0,22 Z" fill="url(#flapBlue)"/>
    </svg>
    <div class="flap-name">TKL Executive Realty</div>
  </section>

  <section class="envelope envelope--front">
    <div class="brand"><span class="brand__mark"></span>TKL Executive Realty</div>
    <address class="envelope__address">2875 Birchwood Lane, Roseville<br>CA 95661-4180</address>
    <div class="footer-rule footer-rule--orange"></div>
    <div class="footer-rule footer-rule--blue"></div>
    <div class="footer-band"></div>
    <span class="tagline">Homes found with care</span>
  </section>

  <div class="option-label option-label--1">Option-1</div>
  <div class="option-label option-label--2">Option-2</div>

</body>
</html>
```